Tallwick Home Services Web Site

Design Web site with 3-4 pages: Home, About Us, Services and Order form / Schedule Appointment (which will likely be link to Method App and Quickbooks integration.)
Services include: Dryer Vent Cleaning, AC Cleaning, Difficult-to-Reach Light Bulb replacement, Wood Repair and Home Maintenance Plans including Fire Safety Checks and Filter Replacement.

Target Market(s)

Luxury Home Owners, Professionals (Dr's/lawyers) and Seniors

Industry/Entity Type

Home Maintenance

Coding

Coded - Design and coding required

Requirements
Must have
• Tagline - Where Home Maintenance is Elementary

```html
<!DOCTYPE html>
<html lang="en">
<head>
<meta charset="utf-8">
<title>Tallwick Home Services</title>
<link href="https://fonts.googleapis.com/css2?family=Montserrat:wght@400;500;600;700&family=Mulish:wght@400;600;700&display=swap" rel="stylesheet">
<style>
:root{
  --gold:#e0a92e;
  --gray:#6d6d6d;
  --gray-mid:#8a8a8a;
  --ink:#3a3a3a;
  --text:#555;
  --line:#d7d7d7;
  --white:#fff;
}
*{box-sizing:border-box;margin:0;padding:0}
html,body{width:1200px;height:4573px;overflow:hidden;background:var(--white)}
body{position:relative;font-family:"Mulish",sans-serif;color:var(--text)}
.abs{position:absolute}
.head{font-family:"Montserrat",sans-serif;font-weight:700}
.btn{position:absolute;display:flex;align-items:center;justify-content:center;border-radius:30px;font-family:"Montserrat",sans-serif;font-weight:700;color:var(--white);letter-spacing:.3px;text-transform:uppercase}
.btn-gold{background:var(--gold)}
.btn-dark{background:var(--gray)}
.photo{position:absolute}

/* header */
.site-header{position:absolute;left:0;top:0;width:1200px;height:111px;background:var(--white)}
.brand{position:absolute;display:flex;align-items:center;gap:10px;font-family:"Montserrat",sans-serif;font-weight:700;color:var(--gold);line-height:1.15}
.brand .mark{flex:none;border-radius:50%;background:var(--gold)}
.main-nav{position:absolute;top:66px;left:427px;display:flex;gap:46px;font-family:"Montserrat",sans-serif;font-weight:600;font-size:14px;color:var(--ink)}
.main-nav .active{border-bottom:3px solid var(--gold);padding-bottom:8px}
.call{position:absolute;left:790px;top:11px;display:flex;align-items:center;gap:10px;font-family:"Montserrat",sans-serif;font-size:15px;color:var(--gray)}
.call i{width:32px;height:32px;border-radius:50%;background:var(--gold);display:flex;align-items:center;justify-content:center}

/* hero */
.hero{position:absolute;left:0;top:111px;width:1200px;height:674px;background:linear-gradient(90deg,#6a6a6a 0%,#777 40%,#9a9a9a 100%)}
.hero-photo{right:0;top:0;width:620px;height:674px;background:linear-gradient(160deg,#d9d5cf 0%,#b7b2ab 45%,#8d8a86 100%)}
.hero-kicker{left:122px;top:180px;font-family:"Montserrat",sans-serif;font-size:20px;color:var(--white);display:flex;align-items:center;gap:12px}
.hero-kicker span{display:inline-block;width:50px;height:1px;background:var(--white)}
.hero-title{left:120px;top:222px;font-size:42px;line-height:48px;color:var(--white)}
.rating{left:126px;top:474px;display:flex;gap:10px;align-items:center;color:var(--white);font-family:"Montserrat",sans-serif;font-size:14px}
.rating .dot{width:34px;height:34px;border-radius:50%;background:var(--white)}
.stars{color:var(--gold);letter-spacing:2px}

/* services */
.sec-title{position:absolute;left:0;width:1200px;text-align:center;font-family:"Montserrat",sans-serif;font-weight:700}
.svc-icon{position:absolute;width:78px;height:78px;border-radius:50%;display:flex;align-items:center;justify-content:center}
.svc-name{position:absolute;font-family:"Montserrat",sans-serif;font-weight:700;font-size:20px;color:var(--ink);line-height:27px}
.svc-desc{position:absolute;font-size:13px;line-height:17px;color:var(--gray-mid);width:240px}
.r{text-align:right}

/* about */
.about{position:absolute;left:0;top:1674px;width:1200px;height:561px}
.about-photo{left:0;top:0;width:612px;height:561px;background:linear-gradient(135deg,#f1f1f1 0%,#d9dde3 50%,#8f9ccc 100%)}
.about-panel{position:absolute;left:612px;top:0;width:588px;height:561px;background:var(--gold)}

/* plans */
.plans-band{position:absolute;left:0;top:2235px;width:1200px;height:510px;background:linear-gradient(180deg,#6c6c6c,#7d7d7d)}
.plan{position:absolute;top:2497px;width:430px;height:460px;background:var(--white);border:1px solid #e3e3e3;border-radius:6px;overflow:hidden;box-shadow:0 2px 8px rgba(0,0,0,.06)}
.plan .img{height:248px}
.plan .bar{position:absolute;left:0;top:278px;width:4px;height:40px;background:var(--gold)}
.plan h3{position:absolute;left:43px;top:278px;font-family:"Montserrat",sans-serif;font-weight:700;font-size:22px;color:var(--ink)}
.plan p{position:absolute;left:42px;top:318px;width:370px;font-size:13px;line-height:21px;color:var(--gray-mid)}
.plan .btn{left:36px;top:375px;width:136px;height:40px;font-size:12px}

/* reviews */
.review-card{position:absolute;left:320px;top:3145px;width:687px;height:330px;border:1.5px solid #cfcfcf;border-radius:6px;background:var(--white)}
.arrow{position:absolute;width:54px;height:54px;border-radius:50%;background:var(--gold);display:flex;align-items:center;justify-content:center}

/* booking */
.booking{position:absolute;left:0;top:3637px;width:1200px;height:618px;background:var(--gold)}
.booking-photo{left:0;top:0;width:570px;height:618px;background:linear-gradient(120deg,#9a8a70 0%,#6d6a5a 45%,#c8b79a 100%)}
.field{position:absolute;height:47px;background:var(--white);border-radius:2px;font-size:13px;color:var(--gray-mid);display:flex;align-items:center;gap:8px;padding-left:16px}
.field.area{align-items:flex-start;padding-top:16px}

/* footer */
.footer-hump{position:absolute;left:488px;top:4222px;width:224px;height:224px;border-radius:50%;background:var(--white)}
.foot-nav{position:absolute;top:4340px;display:flex;gap:30px;font-family:"Montserrat",sans-serif;font-weight:600;font-size:14px;color:var(--ink);align-items:center}
.foot-nav b{width:5px;height:5px;background:var(--ink);display:inline-block}
.rule{position:absolute;left:103px;width:980px;height:1px;background:var(--line)}
.contact{position:absolute;top:4423px;display:flex;gap:12px;align-items:center}
.contact i{width:44px;height:44px;border-radius:50%;background:var(--gold);display:flex;align-items:center;justify-content:center}
.contact small{display:block;font-size:12px;color:var(--gray-mid)}
.contact span{font-size:15px;color:var(--ink)}
.social{position:absolute;width:34px;height:34px;border-radius:50%}
</style>
</head>
<body>

<header class="site-header">
  <div class="brand" style="left:150px;top:34px;font-size:19px"><span class="mark" style="width:30px;height:30px"></span><span>Tallwick<br>Home Services</span></div>
  <nav class="main-nav"><span class="active">HOME</span><span>ABOUT US</span><span>SERVICES</span><span>CONTACT</span></nav>
  <div class="call"><i><svg width="16" height="16" viewBox="0 0 24 24"><path fill="#fff" d="M6.6 10.8a15 15 0 0 0 6.6 6.6l2.2-2.2c.3-.3.7-.4 1-.2 1.1.4 2.3.6 3.6.6.6 0 1 .4 1 1V20c0 .6-.4 1-1 1A17 17 0 0 1 3 4c0-.6.4-1 1-1h3.5c.6 0 1 .4 1 1 0 1.3.2 2.5.6 3.6.1.3 0 .7-.2 1z"/></svg></i>CALL US NOW (+123) 555 0147</div>
  <div class="btn btn-gold" style="left:855px;top:57px;width:228px;height:40px;font-size:13px">Schedule Appointment</div>
</header>

<section class="hero">
  <div class="photo hero-photo" role="img" aria-label="Technician in work gloves replacing a ceiling light bulb"></div>
  <div class="abs hero-kicker">WHERE HOME MAINTENANCE IS ELEMENTARY <span></span></div>
  <h1 class="abs head hero-title">YOUR HOME'S BEST<br>FRIEND FOR SAFETY<br>&amp; MAINTENANCE</h1>
  <div class="btn btn-gold" style="left:118px;top:389px;width:285px;height:55px;font-size:15px">Book an Appointment</div>
  <div class="abs rating"><span class="dot"></span><div>4.9 rating from 220 reviews<br><span class="stars">★★★★★</span></div></div>
</section>

<section>
  <div class="abs" style="left:586px;top:840px;width:28px;height:28px;border-radius:50%;background:var(--gold)"></div>
  <h2 class="sec-title" style="top:892px;font-size:40px;color:var(--gray)">OUR SERVICES</h2>
  <div class="abs" style="left:525px;top:948px;width:166px;height:2px;background:var(--gray-mid)"></div>
  <svg class="abs" style="left:395px;top:1040px" width="440" height="280" viewBox="0 0 440 280"><path d="M8 270 C8 100 110 20 220 20 C330 20 432 100 432 270" fill="none" stroke="var(--gold)" stroke-width="12"/></svg>
  <div class="photo" role="img" aria-label="Technician drilling a wooden drawer" style="left:425px;top:1082px;width:166px;height:228px;background:linear-gradient(160deg,#c9b08a,#8f6f4c)"></div>
  <div class="photo" role="img" aria-label="Worker changing a ceiling light fixture" style="left:612px;top:1082px;width:166px;height:228px;background:linear-gradient(160deg,#e4e6ea,#6f7f9d)"></div>
  <div class="photo" role="img" aria-label="Gloved hands cleaning an air conditioner unit" style="left:425px;top:1333px;width:166px;height:165px;background:linear-gradient(160deg,#eef1f4,#6d93c9)"></div>
  <div class="photo" role="img" aria-label="Technician removing an AC filter" style="left:612px;top:1333px;width:166px;height:165px;background:linear-gradient(160deg,#f0efec,#d3a04a)"></div>

  <div class="svc-icon" style="left:301px;top:1091px;background:var(--gold)"><svg width="34" height="34" viewBox="0 0 24 24" fill="none" stroke="#fff" stroke-width="1.6"><path d="M4 20l9-9M14 4l6 6-3 3-6-6zM4 4l16 16"/></svg></div>
  <div class="svc-name r" style="left:120px;top:1173px;width:247px">Wood Repair</div>
  <div class="svc-desc r" style="left:127px;top:1205px">Lorem ipsum dolor sit amet, consec-tetur adipiscing elit, sed do eiusmo</div>

  <div class="svc-icon" style="left:841px;top:1091px;background:var(--gray)"><svg width="30" height="30" viewBox="0 0 24 24" fill="none" stroke="#fff" stroke-width="1.6"><path d="M9 3h6M12 3v5M8 14a4 4 0 1 0 8 0l-2-6h-4z"/></svg></div>
  <div class="svc-name" style="left:853px;top:1175px;width:260px">Difficult-to-Reach Light<br>Bulb replacement</div>
  <div class="svc-desc" style="left:855px;top:1235px">Lorem ipsum dolor sit amet, consec-tetur adipiscing elit, sed do eiusmo</div>

  <div class="abs" style="left:107px;top:1313px;width:293px;height:1px;background:var(--line)"></div>
  <div class="abs" style="left:822px;top:1313px;width:295px;height:1px;background:var(--line)"></div>

  <div class="svc-icon" style="left:296px;top:1343px;background:var(--gray)"><svg width="30" height="30" viewBox="0 0 24 24" fill="none" stroke="#fff" stroke-width="1.6"><rect x="4" y="3" width="16" height="18" rx="2"/><path d="M7 8h10M7 12h10M7 16h10"/></svg></div>
  <div class="svc-name r" style="left:120px;top:1425px;width:247px">Dryer Vent Cleaning</div>
  <div class="svc-desc r" style="left:127px;top:1457px">Lorem ipsum dolor sit amet, consec-tetur adipiscing elit, sed do eiusmo</div>

  <div class="svc-icon" style="left:836px;top:1343px;background:var(--gold)"><svg width="32" height="32" viewBox="0 0 24 24" fill="none" stroke="#fff" stroke-width="1.6"><rect x="3" y="5" width="18" height="9" rx="1"/><path d="M6 11h12M8 17v3M12 17v3M16 17v3"/></svg></div>
  <div class="svc-name" style="left:848px;top:1425px;width:260px">AC Cleaning</div>
  <div class="svc-desc" style="left:848px;top:1457px">Lorem ipsum dolor sit amet, consec-tetur adipiscing elit, sed do eiusmo</div>

  <div class="btn btn-gold" style="left:465px;top:1547px;width:285px;height:55px;font-size:15px">Book an Appointment</div>
</section>

<section class="about">
  <div class="photo about-photo" role="img" aria-label="Man replacing a ceiling air vent filter"></div>
  <div class="about-panel">
    <h2 class="abs head" style="left:78px;top:100px;font-size:37px;line-height:42px;color:var(--white)">ABOUT TALLWICK<br>HOME SERVICES</h2>
    <p class="abs" style="left:85px;top:230px;width:460px;font-size:18px;line-height:27.5px;color:var(--white)">Lorem ipsum dolor sit amet, consectetur adipisc-ing elit, sed do eiusmod tempor incididunt ut labore et dolore magna aliqua. Quis ipsum sus-pendisse ultrices gravida. Risus commodo viverra maecenas accumsan lacus vel facilisis.</p>
    <div class="btn" style="left:85px;top:393px;width:185px;height:50px;border:2px solid var(--white);font-size:14px">Learn More ›</div>
  </div>
</section>

<section>
  <div class="plans-band" role="img" aria-label="Softened living room backdrop"></div>
  <div class="abs" style="left:586px;top:2288px;width:28px;height:28px;border-radius:50%;background:var(--white)"></div>
  <h2 class="sec-title" style="top:2338px;font-size:34px;color:var(--white)">HOME MAINTENANCE PLANS</h2>
  <div class="abs" style="left:570px;top:2390px;width:60px;height:2px;background:var(--white)"></div>
  <p class="sec-title" style="top:2410px;font-family:'Mulish',sans-serif;font-weight:400;font-size:18px;color:var(--white)">Lorem ipsum dolor sit amet, consectetur adipiscing elit, sed do eiusmod tempor inci</p>

  <article class="plan" style="left:183px">
    <div class="img" role="img" aria-label="Hands fitting a smoke detector to the ceiling" style="background:linear-gradient(160deg,#f3f3f3,#c9bcae)"></div>
    <span class="bar"></span><h3>Fire Safety Checks</h3>
    <p>Lorem ipsum dolor sit amet, consectetur adipiscing elit, sed do eiusmod tempor incididunt ut labore e</p>
    <div class="btn btn-dark">Book Now</div>
  </article>
  <article class="plan" style="left:640px;top:2495px">
    <div class="img" role="img" aria-label="Technician replacing a ceiling vent filter" style="background:linear-gradient(160deg,#e3e0da,#3c4460)"></div>
    <span class="bar"></span><h3>Filter Replacement</h3>
    <p>Lorem ipsum dolor sit amet, consectetur adipiscing elit, sed do eiusmod tempor incididunt ut labore e</p>
    <div class="btn btn-dark">Book Now</div>
  </article>
</section>

<section>
  <p class="sec-title" style="top:3020px;font-family:'Mulish',sans-serif;font-weight:400;font-size:16px;color:var(--gold)">REVIEWS</p>
  <h2 class="sec-title" style="top:3045px;font-size:36px;color:var(--ink)">WHAT PEOPLE SAYS</h2>
  <svg class="abs" style="left:535px;top:3092px" width="130" height="14" viewBox="0 0 130 14"><path d="M3 11 Q65 -2 127 9" fill="none" stroke="var(--gold)" stroke-width="4" stroke-linecap="round"/></svg>
  <div class="review-card">
    <h3 class="abs head" style="left:187px;top:48px;font-size:26px;color:var(--ink)">Excellent Service!</h3>
    <p class="abs" style="left:187px;top:98px;width:450px;font-size:17px;line-height:23px;color:var(--text)">"Lorem ipsum dolor sit amet, consectetur adipisc-ing elit, sed do eiusmod tempor incididunt ut labore et dolore magna aliqua. Quis ipsum sus-pendisse ultrices gravida. Risus commodo viverra maecenas accumsan lacus vel facilisis"</p>
    <div class="abs stars" style="left:187px;top:222px;font-size:22px">★★★★★</div>
    <div class="abs" style="left:195px;top:268px;font-size:15px;font-weight:700;color:var(--ink)">Mara Ellison</div>
    <div class="abs head" style="left:593px;top:220px;font-size:90px;line-height:90px;color:#c9c9c9">”</div>
  </div>
  <div class="abs" style="left:185px;top:3172px;width:276px;height:276px;border-radius:50%;border:4px solid var(--gold);background:var(--white)"></div>
  <div class="photo" role="img" aria-label="Smiling customer giving a thumbs up" style="left:200px;top:3176px;width:260px;height:260px;border-radius:50%;background:linear-gradient(160deg,#e8e6e2,#b7a99a)"></div>
  <div class="arrow" style="left:541px;top:3516px"><svg width="24" height="24" viewBox="0 0 24 24" fill="none" stroke="#fff" stroke-width="2"><path d="M19 12H5M11 6l-6 6 6 6"/></svg></div>
  <div class="arrow" style="left:606px;top:3516px"><svg width="24" height="24" viewBox="0 0 24 24" fill="none" stroke="#fff" stroke-width="2"><path d="M5 12h14M13 6l6 6-6 6"/></svg></div>
</section>

<section class="booking">
  <div class="photo booking-photo" role="img" aria-label="Couple on a sofa booking a visit on a laptop"></div>
  <h2 class="abs head" style="left:630px;top:95px;font-size:37px;line-height:42px;color:var(--white)">BOOK AN<br>APPOINTMENT</h2>
  <div class="field" style="left:632px;top:210px;width:235px">👤 First name</div>
  <div class="field" style="left:878px;top:210px;width:235px">👤 Last name</div>
  <div class="field" style="left:632px;top:269px;width:235px">✆ Email address</div>
  <div class="field" style="left:878px;top:269px;width:235px">✉ Phone</div>
  <div class="field area" style="left:632px;top:328px;width:481px;height:117px">💬 Leave Message</div>
  <div class="btn btn-dark" style="left:632px;top:463px;width:178px;height:50px;font-size:15px">Book Now ›</div>
</section>

<footer>
  <div class="footer-hump"></div>
  <div class="brand" style="left:510px;top:4322px;font-size:22px"><span class="mark" style="width:30px;height:30px"></span><span>Tallwick<br>Home Services</span></div>
  <div class="foot-nav" style="left:110px">HOME<b></b>ABOUT US<b></b>SERVICES</div>
  <div class="foot-nav" style="left:745px">WHY US<b></b>CONTACT<b></b>BOOK NOW</div>
  <div class="rule" style="top:4402px"></div>
  <div class="contact" style="left:125px"><i><svg width="20" height="20" viewBox="0 0 24 24"><path fill="#fff" d="M6.6 10.8a15 15 0 0 0 6.6 6.6l2.2-2.2c.3-.3.7-.4 1-.2 1.1.4 2.3.6 3.6.6.6 0 1 .4 1 1V20c0 .6-.4 1-1 1A17 17 0 0 1 3 4c0-.6.4-1 1-1h3.5c.6 0 1 .4 1 1 0 1.3.2 2.5.6 3.6.1.3 0 .7-.2 1z"/></svg></i><div><small>Phone Number</small><span>(+123) 555 0147</span></div></div>
  <div class="contact" style="left:496px"><i><svg width="20" height="20" viewBox="0 0 24 24" fill="none" stroke="#fff" stroke-width="2"><rect x="3" y="5" width="18" height="14" rx="1"/><path d="M3 6l9 7 9-7"/></svg></i><div><small>Email adress</small><span>info@tallwickhomeservices.com</span></div></div>
  <div class="social" style="left:901px;top:4428px;background:var(--gold)"></div>
  <div class="social" style="left:943px;top:4428px;background:var(--gray)"></div>
  <div class="social" style="left:988px;top:4428px;background:var(--gray)"></div>
  <div class="social" style="left:1031px;top:4428px;background:var(--gray)"></div>
  <div class="rule" style="top:4490px"></div>
  <p class="abs" style="left:0;top:4517px;width:1200px;text-align:center;font-size:13px;color:var(--gray-mid)">Copyright © 2025 Tallwick Home Services . All Right Reserved</p>
  <div class="abs" style="left:977px;top:4510px;width:105px;height:30px;border-radius:15px;background:#e4e4e4;display:flex;align-items:center;justify-content:space-between;padding-left:14px;font-size:10px;font-weight:700;color:var(--gray)">GO TO TOP<span style="width:30px;height:30px;border-radius:50%;background:var(--gray);color:#fff;display:flex;align-items:center;justify-content:center;font-size:14px">↑</span></div>
</footer>

</body>
</html>
```